Website update for Harborline Ledger Partners & Bookkeeping

Our website needs updating
www.harborlineledgerpartners.com
Here are some of our latest print pieces to use as a guide?
I have also attached our graphic identity guide which includes the Pantone colors

Target Market(s)

Insurance Agencies

Industry/Entity Type

Accounting

Number of Pages Required

5+ page

```html
<!DOCTYPE html>
<html lang="en">
<head>
<meta charset="utf-8">
<title>Harborline Ledger Partners &amp; Bookkeeping</title>
<link href="https://fonts.googleapis.com/css2?family=Open+Sans:wght@300;400;600;700&display=swap" rel="stylesheet">
<style>
:root{
  --teal:#18a898;
  --teal-dark:#0f8a7d;
  --teal-deep:#0b6f66;
  --ink:#333b40;
  --muted:#6f7679;
  --line:#e2e6e7;
  --soft:#f3f5f5;
  --white:#ffffff;
  --bar:#2f3437;
}
*{box-sizing:border-box;margin:0;padding:0}
html,body{width:1200px;height:2336px;overflow:hidden}
body{font-family:"Open Sans",Arial,sans-serif;color:var(--ink);background:var(--white);position:relative}
.abs{position:absolute}

/* top bar */
.topbar{left:0;top:0;width:1200px;height:28px;background:var(--bar);color:#cfd4d6;font-size:11px}
.topbar .mail{left:160px;top:7px}
.topbar .social{left:890px;top:6px;display:flex;gap:8px}
.topbar .social span{width:16px;height:16px;background:#555c60;display:block}
.topbar .contact{left:960px;top:0;height:28px;width:110px;background:var(--teal);color:#fff;font-weight:600;text-align:center;line-height:28px}

/* header */
.header{left:0;top:28px;width:1200px;height:68px;background:var(--white)}
.brand{left:160px;top:14px;display:flex;align-items:center;gap:10px}
.brand .mark{width:34px;height:34px;background:var(--teal)}
.brand .name{font-size:15px;font-weight:700;color:var(--teal-deep);line-height:1.15;width:220px}
.callout{left:880px;top:18px;display:flex;align-items:center;gap:12px}
.callout .label{font-size:9px;color:var(--muted);line-height:1.2;text-transform:uppercase;width:80px}
.callout .num{font-size:22px;font-weight:700;color:var(--teal)}
.nav{left:440px;top:96px;width:760px;height:28px;background:var(--teal);display:flex;align-items:center;gap:26px;padding-left:30px;font-size:10.5px;font-weight:600;color:#fff}

/* hero */
.hero{left:0;top:124px;width:1200px;height:596px;background:linear-gradient(100deg,#9aa4a8 0%,#d7dcdd 30%,#eef0f0 55%,#c3cbce 80%,#8f999d 100%)}
.hero .veil{left:0;top:0;width:1200px;height:596px;background:linear-gradient(90deg,rgba(0,0,0,0) 35%,rgba(20,40,45,.45) 100%)}
.hero-copy{left:560px;top:300px;width:480px;text-align:center;color:#fff}
.hero-copy p{font-size:24px;font-weight:300;line-height:1.35}
.hero-copy h1{font-size:56px;font-weight:300;margin-top:8px;line-height:1.1}

/* help band */
.help{left:0;top:720px;width:1200px;height:200px;background:var(--teal)}
.help svg{position:absolute;left:0;top:0}
.help-q{left:150px;top:58px;width:300px;text-align:right}
.help-q small{font-size:15px;color:var(--ink);display:block}
.help-q strong{font-size:26px;font-weight:600;color:var(--teal);line-height:1.25;display:block;margin-top:4px}
.help-list{left:540px;top:34px;width:520px;list-style:none;color:#fff;font-size:11.5px;line-height:1.45}
.help-list li{position:relative;padding-left:16px;margin-bottom:9px}
.help-list li:before{content:"";position:absolute;left:0;top:6px;width:6px;height:6px;background:#fff;border-radius:50%}

/* services */
.services{left:0;top:920px;width:1200px;height:400px;background:var(--soft)}
.section-title{width:1200px;text-align:center;font-size:30px;font-weight:400;color:var(--ink)}
.section-title b{color:var(--teal);font-weight:600}
.services .section-title{top:52px;left:0}
.services .lead{left:320px;top:112px;width:560px;text-align:center;font-size:13px;color:var(--muted);line-height:1.6}
.svc-card{top:232px;width:260px;height:120px;background:var(--white);border:1px solid var(--line);text-align:center}
.svc-card .icon{width:56px;height:40px;margin:20px auto 10px;border-radius:6px}
.svc-card h3{font-size:12.5px;font-weight:600;color:var(--teal);line-height:1.3}
.arrow{top:280px}

/* how it works */
.how{left:0;top:1320px;width:1200px;height:330px;background:var(--white)}
.how h2{left:160px;top:52px;font-size:28px;font-weight:400}
.how h2 b{color:var(--teal);font-weight:600}
.how .intro{left:160px;top:104px;width:220px;font-size:11px;line-height:1.6;color:var(--muted)}
.btn{left:160px;top:200px;width:84px;height:28px;background:var(--teal);color:#fff;font-size:10px;font-weight:600;text-align:center;line-height:28px}
.step{width:296px;height:112px;border:1px solid var(--line);background:var(--white);padding:16px 16px 0 56px}
.step .ic{position:absolute;left:16px;top:16px;width:28px;height:28px}
.step h4{font-size:12px;font-weight:600;color:var(--ink);margin-bottom:6px}
.step p{font-size:10px;line-height:1.5;color:var(--muted)}

/* team */
.team{left:0;top:1650px;width:1200px;height:430px;background:var(--white)}
.team .section-title{top:30px;left:0}
.avatar{border-radius:50%;background:radial-gradient(circle at 50% 40%,#d9cfc8,#a9a09a)}
.team .person{left:400px;top:252px;width:400px;text-align:center}
.person h5{font-size:13px;font-weight:600;color:var(--teal)}
.person span{font-size:10px;color:var(--muted)}
.team .bio{left:260px;top:300px;width:680px;text-align:center;font-size:11px;line-height:1.65;color:var(--muted)}
.dots{left:580px;top:388px;display:flex;gap:8px}
.dots i{width:8px;height:8px;border-radius:50%;background:#c9cfd1;display:block}
.dots i.on{background:var(--teal)}

/* footer */
.footer{left:0;top:2080px;width:1200px;height:220px;background:var(--teal)}
.fcol{top:56px;width:150px;text-align:center;color:#fff}
.fcol .ficon{width:40px;height:40px;border-radius:50%;border:2px solid rgba(255,255,255,.7);margin:0 auto 12px;display:flex;align-items:center;justify-content:center}
.fcol h6{font-size:12px;font-weight:700;margin-bottom:6px}
.fcol p{font-size:10px;line-height:1.5;color:#e5f6f4}
.news{left:820px;top:0;width:300px;height:220px;background:var(--teal-deep);padding:44px 28px;color:#fff}
.news h6{font-size:13px;font-weight:700;margin-bottom:16px}
.news .field{width:240px;height:30px;background:#fff;font-size:10px;color:#9aa1a3;padding:8px 10px}
.news .sub{margin-top:12px;width:80px;height:26px;background:var(--bar);font-size:10px;font-weight:600;text-align:center;line-height:26px}
.copyright{left:0;top:2300px;width:1200px;height:36px;background:#f1f3f3;text-align:center;font-size:10px;color:var(--muted);line-height:36px}
</style>
</head>
<body>

<div class="abs topbar">
  <span class="abs mail">Email: info@harborlineledgerpartners.com</span>
  <div class="abs social"><span></span><span></span><span></span></div>
  <div class="abs contact">Contact Us</div>
</div>

<header class="abs header">
  <div class="abs brand"><div class="mark"></div><div class="name">Harborline Ledger Partners &amp; Bookkeeping</div></div>
  <div class="abs callout"><div class="label">Call us now for assistance</div><div class="num">555-014-7268</div></div>
</header>
<nav class="abs nav"><span>HOME</span><span>ABOUT US</span><span>SERVICES</span><span>OUR TEAM</span><span>WHY IT WORKS</span><span>RESOURCES</span><span>BLOG</span></nav>

<section class="abs hero">
  <div class="abs" role="img" aria-label="Two accountants reviewing documents at a desk in a bright office" style="left:0;top:0;width:1200px;height:596px"></div>
  <div class="abs veil"></div>
  <div class="abs hero-copy">
    <p>Specialists in providing accounting support services to independent</p>
    <h1>Insurance Agencies</h1>
  </div>
</section>

<section class="abs help">
  <svg width="1200" height="200" viewBox="0 0 1200 200"><polygon points="0,0 470,0 510,100 470,200 0,200" fill="#ffffff"/></svg>
  <div class="abs help-q"><small>Need help with your insurance</small><strong>Agency's accounting and bookkeeping?</strong></div>
  <ul class="abs help-list">
    <li>Full service support for insurance agency bookkeeping and reconciliation every single month.</li>
    <li>Team of trained staff with direct agency experience who understand your carriers and your books.</li>
    <li>Reconciled direct bill and agency bill commissions so balances match each statement.</li>
    <li>Reliable monthly reporting and general ledger accounts reviewed by our experienced staff.</li>
  </ul>
</section>

<section class="abs services">
  <h2 class="abs section-title">Services <b>Available</b></h2>
  <p class="abs lead">After working in house at agencies for many years, Marian Voss formed Harborline in 2011 to help independent Insurance Agencies manage their accounting and bookkeeping.</p>
  <svg class="abs arrow" style="left:116px" width="16" height="24" viewBox="0 0 16 24"><polyline points="12,2 3,12 12,22" fill="none" stroke="#9aa1a3" stroke-width="2.5"/></svg>
  <div class="abs svc-card" style="left:210px"><div class="icon" role="img" aria-label="Piggy bank icon" style="background:linear-gradient(#f4b6c2,#e98ea2)"></div><h3>Reconcile Direct<br>Bill Commission</h3></div>
  <div class="abs svc-card" style="left:470px"><div class="icon" role="img" aria-label="Banknotes icon" style="background:linear-gradient(#8fd08a,#57a952)"></div><h3>Reconcile &amp; Pay Agency<br>Bill Premiums</h3></div>
  <div class="abs svc-card" style="left:730px"><div class="icon" role="img" aria-label="Ledger document icon" style="background:linear-gradient(#cfe9e6,#8ccfc7)"></div><h3>Reconcile General<br>Ledger Accounts</h3></div>
  <svg class="abs arrow" style="left:1068px" width="16" height="24" viewBox="0 0 16 24"><polyline points="4,2 13,12 4,22" fill="none" stroke="#9aa1a3" stroke-width="2.5"/></svg>
</section>

<section class="abs how">
  <h2 class="abs">How <b>It Works</b></h2>
  <p class="abs intro">Harborline has the capability to perform all core bookkeeping functions so in house staff can provide focused customer support. Our accountants handle day to day entries and monthly closing.</p>
  <div class="abs btn">VIEW ALL</div>

  <div class="abs step" style="left:410px;top:44px">
    <svg class="ic" viewBox="0 0 28 28"><circle cx="14" cy="9" r="5" fill="#18a898"/><path d="M4 26c0-6 4-9 10-9s10 3 10 9z" fill="#18a898"/></svg>
    <h4>Educated &amp; Trained Staff</h4><p>Our staff hold accounting degrees and are trained on agency systems to deliver accurate and timely work.</p>
  </div>
  <div class="abs step" style="left:722px;top:44px">
    <svg class="ic" viewBox="0 0 28 28"><circle cx="14" cy="14" r="12" fill="none" stroke="#18a898" stroke-width="2.5"/><polyline points="8,14 12,19 20,9" fill="none" stroke="#18a898" stroke-width="2.5"/></svg>
    <h4>Quality Control</h4><p>Every reconciliation is reviewed by a supervisor before it is returned to the agency each month.</p>
  </div>
  <div class="abs step" style="left:410px;top:172px">
    <svg class="ic" viewBox="0 0 28 28"><rect x="3" y="5" width="9" height="18" fill="#18a898"/><rect x="16" y="5" width="9" height="18" fill="none" stroke="#18a898" stroke-width="2.5"/></svg>
    <h4>Separation of Duties</h4><p>Work is divided between preparers and reviewers to provide a system of checks and balances.</p>
  </div>
  <div class="abs step" style="left:722px;top:172px">
    <svg class="ic" viewBox="0 0 28 28"><rect x="5" y="12" width="18" height="14" rx="2" fill="#18a898"/><path d="M9 12V8a5 5 0 0110 0v4" fill="none" stroke="#18a898" stroke-width="2.5"/></svg>
    <h4>Data Security</h4><p>Client records are held on secure encrypted systems with limited access for approved staff only.</p>
  </div>
</section>

<section class="abs team">
  <h2 class="abs section-title">Our <b>Experienced Team</b></h2>
  <div class="abs avatar" role="img" aria-label="Team member portrait" style="left:436px;top:142px;width:44px;height:44px;opacity:.8"></div>
  <div class="abs avatar" role="img" aria-label="Portrait of Marian Voss, principal" style="left:550px;top:120px;width:100px;height:100px;border:4px solid #fff;box-shadow:0 0 0 2px #18a898"></div>
  <div class="abs avatar" role="img" aria-label="Team member portrait" style="left:720px;top:142px;width:44px;height:44px;opacity:.8"></div>
  <div class="abs person"><h5>Marian Voss</h5><span>Principal</span></div>
  <p class="abs bio">Marian spent many years managing the books for independent insurance agencies before founding the firm. She leads a team that reconciles commissions, pays carrier premiums and keeps general ledgers current so agency owners can focus on clients. Her approach combines careful review, clear reporting and prompt communication with every agency the firm supports.</p>
  <div class="abs dots"><i class="on"></i><i></i><i></i></div>
</section>

<footer class="abs footer">
  <div class="abs fcol" style="left:90px">
    <div class="ficon"><svg width="16" height="20" viewBox="0 0 16 20"><path d="M8 1a6 6 0 00-6 6c0 5 6 12 6 12s6-7 6-12a6 6 0 00-6-6z" fill="#fff"/><circle cx="8" cy="7" r="2.2" fill="#18a898"/></svg></div>
    <h6>Address</h6><p>742 Quayside Road<br>Marlow, CT 06000</p>
  </div>
  <div class="abs fcol" style="left:260px">
    <div class="ficon"><svg width="18" height="18" viewBox="0 0 18 18"><path d="M4 1l3 4-2 2c1 2 3 4 5 5l2-2 4 3-2 3C8 16 2 10 1 4z" fill="#fff"/></svg></div>
    <h6>Phone</h6><p>555-014-7268</p>
  </div>
  <div class="abs fcol" style="left:430px">
    <div class="ficon"><svg width="18" height="18" viewBox="0 0 18 18"><rect x="4" y="1" width="10" height="5" fill="#fff"/><rect x="1" y="7" width="16" height="7" fill="#fff"/><rect x="4" y="12" width="10" height="5" fill="#fff" stroke="#18a898"/></svg></div>
    <h6>Fax</h6><p>555-014-7269</p>
  </div>
  <div class="abs fcol" style="left:600px">
    <div class="ficon"><svg width="20" height="14" viewBox="0 0 20 14"><rect x="1" y="1" width="18" height="12" fill="#fff"/><polyline points="1,1 10,8 19,1" fill="none" stroke="#18a898" stroke-width="1.5"/></svg></div>
    <h6>Email</h6><p>info@harborline<br>ledgerpartners.com</p>
  </div>
  <div class="abs news">
    <h6>Subscribe to our Newsletter</h6>
    <div class="field">Enter your email</div>
    <div class="sub">SUBSCRIBE</div>
  </div>
</footer>
<div class="abs copyright">Copyright © 2024 Harborline Ledger Partners &amp; Bookkeeping. All Rights Reserved.</div>

</body>
</html>
```